Business card design needed

The company name is Pellow Architects. We are an architectural company based in Melbourne,Australia that has a mix of client base from health care, commercial office, aged care, multi-residential, single residential and retail. Design type is contemporary.

Suggest the base colours need to be black and white. Please leave an area on the back of the card available for handwritten notes.

Target Market(s)

Generally corporate, aged 30 to 65

Industry/Entity Type

Residential

Contact Information for Business Card

Pellow Architects
Dale Pellow
14 Mosley Street
Fenwick Vale VIC 3074
T (03) 9572 4016
M 0437 619 258
E dp@pellowarc.com.au

Logo Text

PA

Logo styles of interest
Emblem Logo
Abstract Logo
Lettermark Logo
Requirements
Must have
• I am having trouble attaching a sketch so would really appreciate your effort to try the following brief.

Black and White (B&W)
Would like different card cutout profile. Logo Example, use the half circle curve of the G to form the left edge of the card with no margin. The A is to sit inside the G, connected to the G by its horizontal. The A has its cross bar and lower right leg removed. Card in black, text in white.

Back of card to be black text on white background with services provided.

Client Focused Service
Architecture and Design
Functional Planning
Town Planning
Feasability Studies
Contract Documentation
Contract Administration
Project Management

Simple elegant text, Ariel or similar
Nice to have
• Integrated logo and card cut-out.

Card base black on front, white on back
Should not have
• Too many colours
Fussy details

```html
<!DOCTYPE html>
<html lang="en">
<head>
<meta charset="utf-8">
<title>Pellow Architects – Business Card</title>
<link rel="stylesheet" href="https://fonts.googleapis.com/css2?family=Arimo:wght@400;700&display=swap">
<style>
  :root {
    --backdrop: #929598;
    --card-dark: #3d3c3f;
    --card-light: #ffffff;
    --ink-light: #ffffff;
    --ink-dark: #3a3a3c;
    --ink-body: #333333;
    --watermark: #e9e9ea;
  }
  * { margin: 0; padding: 0; box-sizing: border-box; }
  html, body {
    width: 1200px;
    height: 605px;
    overflow: hidden;
    background: var(--backdrop);
    font-family: "Arimo", Arial, sans-serif;
  }
  .canvas { position: relative; width: 1200px; height: 605px; }

  /* Front */
  .card-front__shape { position: absolute; left: 0; top: 0; }
  .card-front__mark {
    position: absolute;
    left: 88px; top: 296px; width: 300px;
    text-align: center;
    font-size: 21px; font-weight: 700;
    color: var(--ink-dark);
  }
  .card-front__title {
    position: absolute;
    left: 392px; top: 212px;
    font-size: 17.5px; font-weight: 700;
    color: var(--ink-light);
    padding-bottom: 4px;
    border-bottom: 2px solid var(--ink-light);
  }
  .card-front__contact {
    position: absolute;
    left: 380px; top: 343px; width: 234px;
    text-align: center;
    font-size: 13.5px; line-height: 17.5px;
    color: var(--ink-light);
  }
  .card-front__address { margin-top: 6px; }

  /* Back */
  .card-back__shape { position: absolute; left: 0; top: 0; }
  .card-back__mark {
    position: absolute;
    left: 840px; top: 360px; width: 220px;
    text-align: center;
    font-size: 20px; font-weight: 700;
    color: var(--watermark);
  }
  .card-back__title {
    position: absolute;
    left: 834px; top: 229px;
    font-size: 17.5px; font-weight: 700;
    color: var(--ink-dark);
    padding-bottom: 3px;
    border-bottom: 2px solid var(--ink-dark);
  }
  .card-back__services {
    position: absolute;
    left: 840px; top: 289px; width: 200px;
    list-style: none;
    text-align: center;
    font-size: 13.5px; line-height: 21.2px;
    color: var(--ink-body);
  }
</style>
</head>
<body>
<main class="canvas">
  <svg class="card-front__shape" width="1200" height="605" aria-hidden="true">
    <rect x="238" y="160" width="386" height="300" fill="var(--card-dark)"/>
    <circle cx="238" cy="310" r="150" fill="var(--card-light)"/>
  </svg>
  <div class="card-front__mark">Pellow Architects</div>
  <h1 class="card-front__title">PELLOW ARCHITECTS</h1>
  <address class="card-front__contact" style="font-style:normal">
    <div>T (03) 9572 4016</div>
    <div>M 0437 619 258</div>
    <div>E dp@pellowarc.com.au</div>
    <div class="card-front__address">Pellow Architects Dale Pellow 14<br>Mosley Street Fenwick Vale VIC 3074</div>
  </address>

  <svg class="card-back__shape" width="1200" height="605" aria-hidden="true">
    <path d="M791 556 V165 A150 150 0 0 1 1091 165 V556 Z" fill="var(--card-light)"/>
    <circle cx="942" cy="332" r="112" fill="none" stroke="var(--watermark)" stroke-width="34"/>
  </svg>
  <div class="card-back__mark">Pellow Architects</div>
  <h2 class="card-back__title">PELLOW ARCHITECTS</h2>
  <ul class="card-back__services">
    <li>Client Focused Service</li>
    <li>Architecture and Design</li>
    <li>Contract Documentation</li>
    <li>Project Management</li>
    <li>Contract Administration</li>
    <li>Functional Planning</li>
    <li>Feasability Studies</li>
    <li>Town Planning</li>
  </ul>
</main>
</body>
</html>
```